Whitcombe Business Card Design

The name of the business is Dario Whitcombe, CPA LLC
The service that we offer is Accounting, Tax & Consulting Services. I need it to have the following items:
Dario Whitcombe, Principal
Phone Number
Email Address
Physical Address

I have attached the company logo, one in black and one in white. Please provide a design in black background and the other in white background. Please include "Accounting, Tax & Consulting Services". I want the business card to be clean and very professional.

```html
<!DOCTYPE html>
<html lang="en">
<head>
<meta charset="utf-8">
<title>Dario Whitcombe, CPA LLC — Business Card</title>
<link href="https://fonts.googleapis.com/css2?family=Montserrat:wght@400;500;600;700&display=swap" rel="stylesheet">
<style>
  :root {
    --canvas: #2a2a2a;
    --card-dark: #1f1f20;
    --card-light: #ffffff;
    --brand-red: #9b1c1f;
    --text-light: #f2f2f2;
    --text-grey: #5e5e60;
    --text-mid: #7a7a7c;
    --text-dark: #2b2b2d;
  }
  * { box-sizing: border-box; margin: 0; padding: 0; }
  html, body { width: 1200px; height: 900px; overflow: hidden; }
  body {
    background: var(--canvas);
    font-family: "Montserrat", sans-serif;
    position: relative;
  }
  .card {
    position: absolute;
    left: 300px;
    width: 600px;
    height: 343px;
    border-radius: 18px;
    overflow: hidden;
    box-shadow: 0 10px 30px rgba(0,0,0,.45);
  }
  .card--front { top: 82px; background: var(--card-dark); }
  .card--back  { top: 475px; background: var(--card-dark); }

  /* Front */
  .front-identity {
    position: absolute;
    left: 130px;
    top: 112px;
  }
  .brand-row { display: flex; align-items: center; gap: 12px; }
  .brand-square {
    width: 22px; height: 22px;
    background: var(--brand-red);
  }
  .brand-name {
    font-weight: 600;
    font-size: 29px;
    letter-spacing: .5px;
    color: var(--text-grey);
    white-space: nowrap;
  }
  .front-title {
    margin-top: 10px;
    margin-left: 34px;
    font-weight: 600;
    font-size: 19px;
    letter-spacing: 3px;
    color: #8a8a8c;
  }
  .front-services {
    margin-top: 12px;
    margin-left: 34px;
    font-weight: 700;
    font-size: 15px;
    color: var(--text-mid);
  }

  /* Back */
  .back-light {
    position: absolute;
    left: 0; top: 0; bottom: 0;
    width: 262px;
    background: var(--card-light);
  }
  .back-brand {
    position: absolute;
    left: 0; width: 262px;
    top: 142px;
    text-align: center;
  }
  .back-brand .brand-row { justify-content: center; gap: 7px; }
  .back-brand .brand-square { width: 12px; height: 12px; }
  .back-brand .brand-name { font-size: 15px; font-weight: 600; color: var(--text-dark); letter-spacing: 0; }
  .back-brand .back-title {
    margin-top: 5px;
    font-size: 9px;
    letter-spacing: 2px;
    color: var(--text-mid);
    font-weight: 500;
  }
  .name-band {
    position: absolute;
    left: 262px; right: 0;
    top: 78px;
    height: 40px;
    background: var(--brand-red);
    color: var(--text-light);
    font-weight: 700;
    font-size: 16px;
    letter-spacing: .3px;
    display: flex; align-items: center;
    padding-left: 22px;
  }
  .contact-list {
    position: absolute;
    left: 282px; top: 140px;
    list-style: none;
  }
  .contact-item {
    display: flex;
    align-items: flex-start;
    gap: 12px;
    color: var(--text-light);
    font-size: 12.5px;
    font-weight: 500;
    line-height: 1.45;
    margin-bottom: 11px;
  }
  .contact-icon {
    flex: 0 0 22px;
    width: 22px; height: 22px;
  }
</style>
</head>
<body>

<section class="card card--front" aria-label="Business card front">
  <div class="front-identity">
    <div class="brand-row">
      <span class="brand-square"></span>
      <span class="brand-name">Dario Whitcombe, CPA LLC</span>
    </div>
    <p class="front-title">CERTIFIED PUBLIC ACCOUNTANT</p>
    <p class="front-services">Accounting, Tax &amp; Consulting Services</p>
  </div>
</section>

<section class="card card--back" aria-label="Business card back">
  <div class="back-light"></div>
  <div class="back-brand">
    <div class="brand-row">
      <span class="brand-square"></span>
      <span class="brand-name">Dario Whitcombe, CPA LLC</span>
    </div>
    <p class="back-title">CERTIFIED PUBLIC ACCOUNTANT</p>
  </div>

  <div class="name-band">DARIO WHITCOMBE, PRINCIPAL</div>

  <ul class="contact-list">
    <li class="contact-item">
      <svg class="contact-icon" viewBox="0 0 22 22" aria-hidden="true">
        <circle cx="11" cy="11" r="11" fill="var(--brand-red)"/>
        <path d="M11 4.5a4 4 0 0 0-4 4c0 3 4 8 4 8s4-5 4-8a4 4 0 0 0-4-4z" fill="#fff"/>
        <circle cx="11" cy="8.5" r="1.5" fill="var(--brand-red)"/>
      </svg>
      <span>#27-C, Larkspur Trade Court,<br>Fenwick Road, Halden, 410228</span>
    </li>
    <li class="contact-item">
      <svg class="contact-icon" viewBox="0 0 22 22" aria-hidden="true">
        <circle cx="11" cy="11" r="11" fill="var(--brand-red)"/>
        <path d="M7.5 5.5l2 2.2-1.1 1.6a7 7 0 0 0 3.3 3.3l1.6-1.1 2.2 2-1.3 2.1c-4 .2-8.8-4.6-8.6-8.6z" fill="#fff"/>
      </svg>
      <span>555-204-7391</span>
    </li>
    <li class="contact-item">
      <svg class="contact-icon" viewBox="0 0 22 22" aria-hidden="true">
        <circle cx="11" cy="11" r="11" fill="var(--brand-red)"/>
        <rect x="5.5" y="7" width="11" height="8" fill="#fff"/>
        <path d="M5.5 7l5.5 4.5L16.5 7" fill="none" stroke="var(--brand-red)" stroke-width="1.2"/>
      </svg>
      <span>info@whitcombecpa.com</span>
    </li>
    <li class="contact-item">
      <svg class="contact-icon" viewBox="0 0 22 22" aria-hidden="true">
        <circle cx="11" cy="11" r="11" fill="var(--brand-red)"/>
        <circle cx="11" cy="11" r="5.5" fill="none" stroke="#fff" stroke-width="1.3"/>
        <ellipse cx="11" cy="11" rx="2.4" ry="5.5" fill="none" stroke="#fff" stroke-width="1.1"/>
        <line x1="5.5" y1="11" x2="16.5" y2="11" stroke="#fff" stroke-width="1.1"/>
      </svg>
      <span>www.whitcombecpa.com</span>
    </li>
  </ul>
</section>

</body>
</html>
```